Coastline Premier Retreats Business Card Design

Design a business card for Coastline Premier Retreats. Look at the website for colors and reference. Card should have logo, name, title, office number, mobile number, email, URL and a tagline like, "Luxury Hotel & Resort Email Marketing" (This might change).

https://www.coastlinepremierretreats.example

The rest I will leave up to your imagination.

Contact Information for Business Card

Logo, name, title, office number, mobile number, email, URL and a tagline like, "Luxury Hotel & Resort Email Marketing" (This might change).

```html
<!DOCTYPE html>
<html lang="en">
<head>
<meta charset="utf-8">
<title>Coastline Premier Retreats – Business Card</title>
<link href="https://fonts.googleapis.com/css2?family=Arimo:wght@400;700&display=swap" rel="stylesheet">
<style>
  :root {
    --stage: #2b2b2d;
    --card-dark: #050505;
    --card-light: #f6f6f6;
    --accent: #f07d14;
    --ink: #151515;
    --muted: #6e6e6e;
    --white: #ffffff;
  }
  * { box-sizing: border-box; margin: 0; padding: 0; }
  html, body {
    width: 1200px; height: 912px; overflow: hidden;
    background: var(--stage);
    font-family: "Arimo", Arial, sans-serif;
  }
  .stage {
    position: relative; width: 1200px; height: 912px;
    display: flex; flex-direction: column; align-items: center; justify-content: center; gap: 36px;
  }
  .card {
    position: relative; width: 660px; height: 377px;
    border-radius: 22px; overflow: hidden;
  }
  /* Back side */
  .card--back { background: var(--card-dark); color: var(--white); }
  .brand {
    position: absolute; left: 0; right: 0;
    display: flex; align-items: center; justify-content: center; gap: 14px;
    font-weight: 700; letter-spacing: 0.02em; text-transform: uppercase;
  }
  .brand__square { width: 18px; height: 18px; background: var(--accent); flex: none; }
  .card--back .brand { top: 150px; font-size: 30px; color: var(--white); }
  .back-url {
    position: absolute; left: 0; right: 0; top: 290px; text-align: center;
    font-size: 15px; letter-spacing: 0.14em; color: var(--white);
  }
  .back-url .accent { color: var(--accent); }

  /* Front side */
  .card--front { background: var(--card-light); color: var(--ink); }
  .card--front .brand {
    left: auto; right: 40px; top: 44px; justify-content: flex-end;
    font-size: 19px; color: var(--ink);
  }
  .company-block { position: absolute; right: 40px; top: 150px; width: 330px; text-align: right; }
  .tagline { font-size: 15px; color: var(--ink); padding-bottom: 8px; border-bottom: 1px solid var(--ink); }
  .contact-line {
    display: flex; justify-content: flex-end; align-items: center; gap: 8px;
    font-size: 14px; margin-top: 7px; color: var(--ink);
  }
  .icon { width: 13px; height: 13px; flex: none; }
  .person { position: absolute; left: 40px; bottom: 40px; width: 240px; }
  .person__name { font-size: 25px; font-weight: 700; color: var(--ink); }
  .person__title { font-size: 16px; color: var(--muted); margin-top: 2px; padding-bottom: 8px; border-bottom: 1px solid var(--ink); }
  .phone-line { display: flex; align-items: center; gap: 10px; font-size: 18px; margin-top: 6px; color: var(--ink); }
  .phone-line .icon { width: 16px; height: 16px; }
</style>
</head>
<body>
<main class="stage">
  <section class="card card--back" aria-label="Card back">
    <div class="brand"><span class="brand__square"></span>Coastline Premier Retreats</div>
    <p class="back-url">www.<span class="accent">coastlinepremierretreats</span>.example</p>
  </section>

  <section class="card card--front" aria-label="Card front">
    <div class="brand"><span class="brand__square"></span>Coastline Premier Retreats</div>

    <div class="company-block">
      <p class="tagline">Luxury Hotel &amp; Resort Email Marketing</p>
      <p class="contact-line">info@coastlinepremierretreats.example
        <svg class="icon" viewBox="0 0 16 16" aria-hidden="true"><rect x="1" y="3" width="14" height="10" rx="1" fill="var(--accent)"/><path d="M1.5 4 8 9l6.5-5" stroke="var(--white)" stroke-width="1.4" fill="none"/></svg>
      </p>
      <p class="contact-line">www.coastlinepremierretreats.example
        <svg class="icon" viewBox="0 0 16 16" aria-hidden="true"><circle cx="8" cy="8" r="7" fill="var(--accent)"/><path d="M1 8h14M8 1c-3 3.5-3 10.5 0 14M8 1c3 3.5 3 10.5 0 14" stroke="var(--white)" stroke-width="1.1" fill="none"/></svg>
      </p>
    </div>

    <div class="person">
      <p class="person__name">Daniel Reyes</p>
      <p class="person__title">President</p>
      <p class="phone-line">
        <svg class="icon" viewBox="0 0 16 16" aria-hidden="true"><path d="M3.5 1.5 6 4 4.6 5.8c.8 2 2.6 3.8 4.6 4.6L11 9l2.5 2.5-1.6 2.2C7 13.5 2.5 9 2.3 3.1z" fill="var(--accent)"/></svg>
        555.014.2200
      </p>
      <p class="phone-line">
        <svg class="icon" viewBox="0 0 16 16" aria-hidden="true"><rect x="4" y="1" width="8" height="14" rx="1.5" fill="none" stroke="var(--accent)" stroke-width="1.6"/><circle cx="8" cy="12.5" r="0.9" fill="var(--accent)"/></svg>
        555.014.2201
      </p>
    </div>
  </section>
</main>
</body>
</html>
```